I have a basic design of a poster that I want to make look better. The poster is a list of continuing medical education rules.

HBCPR = Harlowe Board for Clinical Practice Review This text should be included. You might also want to include "CME". Please use all the existing elements in the file.

I want to sell this poster to CME offices around the US. The poster should be 24 by 36

Reason: I would like to see more designs. I have received less than ten.

Target Market(s)

CME professionals

Industry/Entity Type

Medical

Colors

Designer to choose colors to be used in the design.

Requirements
Must have
• All elements in the file provided. You can also spell out Harlowe Board for Clinical Practice Review.

```html
<!DOCTYPE html>
<html lang="en">
<head>
<meta charset="UTF-8">
<title>HBCPR Accreditation Criteria</title>
<link href="https://fonts.googleapis.com/css2?family=Anton&family=Oswald:wght@400;500;600&family=Roboto+Condensed:wght@400;500&display=swap" rel="stylesheet">
<style>
  :root {
    --plum-deep: #5a1d5c;
    --plum: #7d2f7f;
    --plum-band: #8c3b8d;
    --lilac: #dcc4e0;
    --lilac-soft: #e8d7ea;
    --ink: #3a1a3b;
    --white: #ffffff;
  }
  * { box-sizing: border-box; margin: 0; padding: 0; }
  html, body { width: 800px; height: 1200px; overflow: hidden; background: var(--white); }
  .poster { position: relative; width: 800px; height: 1200px; background: var(--white); overflow: hidden; }

  .masthead { position: absolute; left: 0; top: 0; width: 800px; height: 124px; background: var(--plum-deep); }
  .masthead-accent { position: absolute; right: 0; top: 0; width: 250px; height: 124px;
    background: linear-gradient(135deg, rgba(140,59,141,0) 10%, #9a4a9b 70%, #b06ab1 100%); }
  .masthead-title {
    position: absolute; left: 34px; top: 26px; z-index: 1;
    font-family: "Anton", sans-serif; font-weight: 400; font-size: 60px; line-height: 1; color: var(--white);
    white-space: nowrap; transform: scaleX(0.72); transform-origin: left top;
  }

  .intro-band { position: absolute; left: 0; top: 124px; width: 800px; height: 152px; background: var(--plum-band); }
  .intro-label {
    position: absolute; left: 246px; top: 14px; width: 308px; height: 38px;
    background: var(--white); border: 2px solid var(--plum-deep);
    font-family: "Oswald", sans-serif; font-weight: 400; font-size: 27px; color: var(--plum);
    text-align: center; line-height: 34px; letter-spacing: 0.5px;
  }
  .intro-text {
    position: absolute; left: 30px; top: 64px; width: 740px;
    font-family: "Roboto Condensed", sans-serif; font-size: 14.5px; line-height: 1.45; color: var(--white);
    text-align: center; font-weight: 500;
  }

  .criteria-grid {
    position: absolute; left: 21px; top: 286px; width: 758px;
    display: grid; grid-template-columns: repeat(3, 238px); grid-auto-rows: 120px;
    column-gap: 22px; row-gap: 20px;
  }
  .criterion { background: var(--lilac); position: relative; padding: 35px 10px 6px; overflow: hidden; }
  .criterion-tag {
    position: absolute; left: 50%; top: 6px; transform: translateX(-50%);
    width: 128px; height: 24px; background: var(--plum);
    font-family: "Oswald", sans-serif; font-weight: 500; font-size: 15px; color: var(--white);
    text-align: center; line-height: 24px;
  }
  .criterion-text {
    font-family: "Roboto Condensed", sans-serif; font-size: 10.8px; line-height: 1.25; color: var(--ink);
    text-align: justify;
  }
  .criterion-text.centered { text-align: center; padding-top: 8px; }

  .commendation-band {
    position: absolute; left: 0; top: 974px; width: 800px; height: 44px; background: var(--plum-deep);
    font-family: "Oswald", sans-serif; font-weight: 600; font-size: 27px; color: var(--white);
    text-align: center; line-height: 44px; letter-spacing: 1px;
  }
  .commendation-row {
    position: absolute; left: 21px; top: 1026px; width: 758px;
    display: grid; grid-template-columns: repeat(7, 1fr); column-gap: 10px;
  }
  .commendation { background: var(--lilac-soft); height: 121px; padding: 28px 6px 6px; position: relative; overflow: hidden; }
  .commendation .criterion-tag { width: 86px; height: 20px; line-height: 20px; font-size: 12px; top: 6px; }
  .commendation .criterion-text { font-size: 8.6px; line-height: 1.3; text-align: center; }

  .footer { position: absolute; left: 0; top: 1159px; width: 800px; height: 41px; background: var(--plum-deep);
    font-family: "Roboto Condensed", sans-serif; font-size: 17px; font-weight: 500; color: var(--white);
    text-align: center; line-height: 41px; letter-spacing: 0.5px; }
</style>
</head>
<body>
<main class="poster">
  <header class="masthead">
    <div class="masthead-accent" role="img" aria-label="Decorative pattern of stacked purple squares"></div>
    <h1 class="masthead-title">HBCPR ACCREDITATION CRITERIA</h1>
  </header>

  <section class="intro-band">
    <h2 class="intro-label">ACCREDITATION CRITERIA</h2>
    <p class="intro-text">The Accreditation Criteria are divided into three levels. To achieve Provisional Accreditation, a two year term, providers must comply with Criteria 1, 2, 3, and 7-12. Providers seeking full Accreditation or reaccreditation for a four-year term must comply with Criteria 1-13. To achieve Accreditation with Commendation, a six-year term, providers must comply with all Accreditation Criteria 1-22.</p>
  </section>

  <section class="criteria-grid">
    <article class="criterion"><h3 class="criterion-tag">Criterion 1</h3><p class="criterion-text">The provider has a CME mission statement that includes expected results articulated in terms of changes in competence, performance, or patient outcomes that will be the result of the program.</p></article>
    <article class="criterion"><h3 class="criterion-tag">Criterion 2</h3><p class="criterion-text">The provider incorporates into CME activities the educational needs (knowledge, competence, or performance) that underlie the professional practice gaps of their own learners.</p></article>
    <article class="criterion"><h3 class="criterion-tag">Criterion 3</h3><p class="criterion-text">The provider generates activities/educational interventions that are designed to change competence, performance, or patient outcomes as described in its mission statement.</p></article>

    <article class="criterion"><h3 class="criterion-tag">Criterion 4</h3><p class="criterion-text centered">This criterion has been eliminated effective February 2014.</p></article>
    <article class="criterion"><h3 class="criterion-tag">Criterion 5</h3><p class="criterion-text">The provider chooses educational formats for activities/interventions that are appropriate for the setting, objectives, and desired results of the activity.</p></article>
    <article class="criterion"><h3 class="criterion-tag">Criterion 6</h3><p class="criterion-text">The provider develops activities/ educational interventions in the context of desirable physician attributes [eg, Northfield Institute of Clinical Sciences (NICS) competencies, Council for Residency Training Review (CRTR) Competencies].</p></article>

    <article class="criterion"><h3 class="criterion-tag">Criterion 7</h3><p class="criterion-text">The provider develops activities/educational interventions independent of commercial interests. (SCS 1, 2, and 6).</p></article>
    <article class="criterion"><h3 class="criterion-tag">Criterion 8</h3><p class="criterion-text">The provider appropriately manages commercial support (if applicable, SCS 3 of the HBCPR Standards for Commercial Support).</p></article>
    <article class="criterion"><h3 class="criterion-tag">Criterion 9</h3><p class="criterion-text">The provider maintains a separation of promotion from education (SCS 4).</p></article>

    <article class="criterion"><h3 class="criterion-tag">Criterion 10</h3><p class="criterion-text">The provider actively promotes improvements in health care and NOT proprietary interests of a commercial interest (SCS 5).</p></article>
    <article class="criterion"><h3 class="criterion-tag">Criterion 11</h3><p class="criterion-text">The provider analyzes changes in learners (competence, performance, or patient outcomes) achieved as a result of the overall program's activities/educational interventions.</p></article>
    <article class="criterion"><h3 class="criterion-tag">Criterion 12</h3><p class="criterion-text">The provider gathers data or information and conducts a program-based analysis on the degree to which the CME mission of the provider has been met through the conduct of CME activities/educational interventions.</p></article>

    <article class="criterion"><h3 class="criterion-tag">Criterion 13</h3><p class="criterion-text">The provider identifies, plans and implements the needed or desired changes in the overall program (eg, planners, teachers, infrastructure, methods, resources, facilities, interventions) that are required to improve on ability to meet the CME mission.</p></article>
    <article class="criterion"><h3 class="criterion-tag">Criterion 14</h3><p class="criterion-text centered">This criterion has been eliminated effective February 2014.</p></article>
    <article class="criterion"><h3 class="criterion-tag">Criterion 15</h3><p class="criterion-text centered">This criterion has been eliminated effective February 2014.</p></article>
  </section>

  <h2 class="commendation-band">ACCREDITATION WITH COMMENDATION</h2>

  <section class="commendation-row">
    <article class="commendation"><h3 class="criterion-tag">Criterion 16</h3><p class="criterion-text">The provider operates in a manner that integrates CME into the process for improving professional practice.</p></article>
    <article class="commendation"><h3 class="criterion-tag">Criterion 17</h3><p class="criterion-text">The provider utilizes non-education strategies to enhance change as an adjunct to its activities/ educational interventions (e.g., reminders, patient feedback).</p></article>
    <article class="commendation"><h3 class="criterion-tag">Criterion 18</h3><p class="criterion-text">The provider identifies factors outside the provider's control that impact on patient outcomes.</p></article>
    <article class="commendation"><h3 class="criterion-tag">Criterion 19</h3><p class="criterion-text">The provider implements educational strategies to remove, overcome or address barriers to physician change.</p></article>
    <article class="commendation"><h3 class="criterion-tag">Criterion 20</h3><p class="criterion-text">The provider builds bridges with other stakeholders through collaboration and cooperation.</p></article>
    <article class="commendation"><h3 class="criterion-tag">Criterion 21</h3><p class="criterion-text">The provider participates within an institutional or system framework for quality improvement.</p></article>
    <article class="commendation"><h3 class="criterion-tag">Criterion 22</h3><p class="criterion-text">The provider is positioned to influence the scope and content of activities/educational interventions.</p></article>
  </section>

  <footer class="footer">www.hbcpr.org</footer>
</main>
</body>
</html>
```